Business card for law firm

Need business card for new law firm. Think confident, authoritative, conservative, but not stuffy or old-fashioned.

Contact Information for Business Card

Content for card - logo (uploaded), plus the following:

Paul Whitcombe (larger font)
Managing Partner (larger font, but not as large as name)
Level 9, 7 Ferris Lane
Sydney NSW 2000
Main Tel 02 9364 2710
Direct Tel 02 8472 3159
Email paul@qvlegal.com.au
www.qvlegal.com.au

Letterhead design should include logo plus:
Level 9, 7 Ferris Lane
Sydney NSW 2000
Tel 02 8472 3159
www.qvlegal.com.au

```html
<!DOCTYPE html>
<html lang="en">
<head>
<meta charset="utf-8">
<title>Quayvale Lawyers – Business Card</title>
<link rel="stylesheet" href="https://fonts.googleapis.com/css2?family=Merriweather:wght@400;700&display=swap">
<style>
  :root {
    --navy: #1f2452;
    --white: #ffffff;
    --backdrop: #e6e8e9;
    --rule: #d9dbe6;
    --serif: "Merriweather", Georgia, serif;
  }
  * { box-sizing: border-box; margin: 0; padding: 0; }
  html, body {
    width: 1154px;
    height: 1200px;
    overflow: hidden;
    background: var(--backdrop);
    font-family: var(--serif);
  }
  .sheet {
    position: relative;
    width: 1154px;
    height: 1200px;
  }
  .card {
    position: absolute;
    top: 190px;
    width: 500px;
    height: 820px;
    background: var(--white);
    border-radius: 18px;
    overflow: hidden;
    box-shadow: 0 3px 10px rgba(0,0,0,0.12);
  }
  .card--front { left: 50px; }
  .card--back  { left: 604px; }

  /* Front */
  .front-brand {
    position: absolute;
    top: 300px;
    left: 0;
    width: 100%;
    text-align: center;
    color: var(--navy);
    font-weight: 400;
  }
  .brand-square {
    display: block;
    width: 64px;
    height: 64px;
    margin: 0 auto 34px;
    background: var(--navy);
  }
  .front-brand .firm-name {
    font-size: 54px;
    letter-spacing: 2px;
    line-height: 1;
  }
  .front-brand .firm-type {
    margin-top: 16px;
    font-size: 22px;
    letter-spacing: 30px;
    padding-left: 30px;
  }

  /* Back */
  .band {
    position: absolute;
    left: 0;
    width: 100%;
    background: var(--navy);
    color: var(--white);
    text-align: center;
  }
  .band--header { top: 30px; height: 118px; padding-top: 20px; }
  .band--header .firm-name {
    font-size: 44px;
    letter-spacing: 2px;
    line-height: 1;
  }
  .band--header .firm-type {
    margin-top: 10px;
    font-size: 15px;
    letter-spacing: 22px;
    padding-left: 22px;
  }
  .back-square {
    position: absolute;
    top: 212px;
    left: 188px;
    width: 124px;
    height: 124px;
    background: var(--navy);
  }
  .contact-block {
    position: absolute;
    top: 408px;
    left: 0;
    width: 100%;
    height: 380px;
    background: var(--navy);
    color: var(--white);
    text-align: center;
  }
  .contact-row {
    display: flex;
    flex-direction: column;
    justify-content: center;
    border-bottom: 2px solid var(--rule);
  }
  .contact-row:last-child { border-bottom: none; }
  .contact-row--name { height: 92px; }
  .contact-row--phone { height: 92px; }
  .contact-row--web { height: 92px; }
  .contact-row--address { height: 104px; }
  .person-name { font-size: 31px; font-weight: 700; line-height: 1.2; }
  .person-title { font-size: 22px; font-weight: 700; line-height: 1.2; }
  .contact-line { font-size: 21px; line-height: 1.35; }
  .contact-line small { font-size: 12px; margin-left: 4px; }
  .address-line { font-size: 20px; line-height: 1.4; letter-spacing: 0.5px; }
</style>
</head>
<body>
<main class="sheet">
  <section class="card card--front" aria-label="Card front">
    <div class="front-brand">
      <span class="brand-square"></span>
      <div class="firm-name">QUAYVALE</div>
      <div class="firm-type">LAWYERS</div>
    </div>
  </section>

  <section class="card card--back" aria-label="Card back">
    <header class="band band--header">
      <div class="firm-name">QUAYVALE</div>
      <div class="firm-type">LAWYERS</div>
    </header>
    <span class="back-square"></span>
    <div class="contact-block">
      <div class="contact-row contact-row--name">
        <div class="person-name">Paul Whitcombe</div>
        <div class="person-title">Managing Partner</div>
      </div>
      <div class="contact-row contact-row--phone">
        <div class="contact-line">02 9364 2710<small>(main)</small></div>
        <div class="contact-line">02 8472 3159<small>(direct)</small></div>
      </div>
      <div class="contact-row contact-row--web">
        <div class="contact-line">paul@qvlegal.com.au</div>
        <div class="contact-line">www.qvlegal.com.au</div>
      </div>
      <div class="contact-row contact-row--address">
        <div class="address-line">LEVEL 9, 7 FERRIS LANE</div>
        <div class="address-line">SYDNEY • NSW • 2000</div>
      </div>
    </div>
  </section>
</main>
</body>
</html>
```